Telecommunications/Power civil contractor needs business card design

Were a new telecommunications/power underground civil contractor that is looking for a new business card design. Our company colours are silver or grey and orange. Feel free to use the white background logo or the black background logo.

Target Market(s)

Local contractors, utility companies, private sector mining/energy companies, developers.

Industry/Entity Type

Telecommunications

Contact Information for Business Card

Each card will need the following info:
Persons name:
Title:
E-mail:
Phone number:
Shop Address:
Mailing Address:

Requirements
Must have
• Each card will need the following info:
• Persons name:
• Title:
• E-mail:
• Phone number:
• Shop Address:
• Mailing Address:

```html
<!DOCTYPE html>
<html lang="en">
<head>
<meta charset="utf-8">
<title>Ridgeline Civil Works – Business Card</title>
<link rel="stylesheet" href="https://fonts.googleapis.com/css2?family=Arimo:wght@400;700&family=Tinos:wght@700&display=swap">
<style>
  :root {
    --stage: #262626;
    --card-top: #070707;
    --card-top-edge: #151515;
    --divider: #767676;
    --card-body: #585858;
    --card-body-deep: #4b4b4b;
    --text-light: #dcdcdc;
    --text-soft: #c9c9c9;
    --accent-orange: #e8622a;
  }
  * { margin: 0; padding: 0; box-sizing: border-box; }
  html, body {
    width: 1200px;
    height: 997px;
    overflow: hidden;
    background: var(--stage);
    font-family: "Arimo", Arial, sans-serif;
  }
  .business-card {
    position: absolute;
    left: 150px;
    top: 241px;
    width: 900px;
    height: 514px;
    border-radius: 26px;
    overflow: hidden;
    background: linear-gradient(180deg, var(--card-body) 0%, var(--card-body-deep) 100%);
  }
  .card-header {
    position: absolute;
    left: 0; top: 0;
    width: 100%;
    height: 206px;
    background: linear-gradient(180deg, var(--card-top-edge) 0%, var(--card-top) 100%);
  }
  .header-divider {
    position: absolute;
    left: 0; top: 206px;
    width: 100%;
    height: 7px;
    background: var(--divider);
  }
  .divider-notch {
    position: absolute;
    left: 54px;
    top: 213px;
    width: 28px;
    height: 14px;
  }
  .brand {
    position: absolute;
    left: 0; top: 58px;
    width: 100%;
    display: flex;
    flex-direction: column;
    align-items: center;
    gap: 18px;
  }
  .brand-dot {
    width: 62px;
    height: 62px;
    border-radius: 50%;
    border: 5px solid var(--accent-orange);
  }
  .brand-name {
    font-weight: 700;
    font-size: 34px;
    letter-spacing: 2px;
    color: var(--accent-orange);
  }
  .holder {
    position: absolute;
    left: 58px;
    top: 252px;
  }
  .holder-name {
    font-size: 32px;
    color: var(--text-light);
    font-weight: 400;
  }
  .holder-title {
    margin-top: 6px;
    font-family: "Tinos", "Times New Roman", serif;
    font-weight: 700;
    font-size: 19px;
    color: var(--text-soft);
  }
  .company-details {
    position: absolute;
    right: 46px;
    top: 250px;
    text-align: right;
    color: var(--text-soft);
  }
  .company-name {
    font-size: 23px;
    margin-bottom: 14px;
    color: var(--text-light);
  }
  .detail-line {
    display: flex;
    justify-content: flex-end;
    align-items: center;
    gap: 12px;
    font-size: 18px;
    line-height: 30px;
  }
  .contact-list {
    position: absolute;
    left: 58px;
    top: 398px;
    color: var(--text-soft);
    list-style: none;
  }
  .contact-list li {
    display: flex;
    align-items: center;
    gap: 14px;
    font-size: 20px;
    line-height: 38px;
  }
  .icon { width: 18px; height: 18px; fill: var(--text-soft); flex: none; }
</style>
</head>
<body>
  <section class="business-card" aria-label="Business card">
    <div class="card-header"></div>
    <div class="header-divider"></div>
    <svg class="divider-notch" viewBox="0 0 28 14" aria-hidden="true"><polygon points="0,0 28,0 14,14" fill="var(--divider)"/></svg>

    <div class="brand">
      <div class="brand-dot"></div>
      <div class="brand-name">RIDGELINE CIVIL</div>
    </div>

    <div class="holder">
      <h1 class="holder-name">Daniel Whitcombe</h1>
      <p class="holder-title">Owner</p>
    </div>

    <div class="company-details">
      <p class="company-name">Ridgeline Civil Works Inc.</p>
      <p class="detail-line">Unit 14, Depot Road, Ashford
        <svg class="icon" viewBox="0 0 20 20" aria-hidden="true"><path d="M10 2 1 10h3v8h4.5v-5h3v5H16v-8h3z"/></svg>
      </p>
      <p class="detail-line">22 Birch Hollow Drive, Milton, CT 06500
        <svg class="icon" viewBox="0 0 20 20" aria-hidden="true"><path d="M10 1a6 6 0 0 0-6 6c0 4.5 6 12 6 12s6-7.5 6-12a6 6 0 0 0-6-6zm0 8.3A2.3 2.3 0 1 1 10 4.7a2.3 2.3 0 0 1 0 4.6z"/></svg>
      </p>
    </div>

    <ul class="contact-list">
      <li>
        <svg class="icon" viewBox="0 0 20 20" aria-hidden="true"><path d="M4.5 1.5 8 5 6 7.5c1 2.5 3.5 5 6 6l2.5-2 3.5 3.5-2.5 3C8 17.5 2.5 12 1.5 4z"/></svg>
        0412 555 308
      </li>
      <li>
        <svg class="icon" viewBox="0 0 20 20" aria-hidden="true"><path d="M1 4h18v12H1zm1.6 1.4L10 11l7.4-5.6z"/></svg>
        daniel@ridgelinecivil.com
      </li>
    </ul>
  </section>
</body>
</html>
```